Telecommunications/Power civil contractor needs business card design

Were a new telecommunications/power underground civil contractor that is looking for a new business card design. Our company colours are silver or grey and orange. Feel free to use the white background logo or the black background logo.

Target Market(s)

Local contractors, utility companies, private sector mining/energy companies, developers.

Industry/Entity Type

Telecommunications

Contact Information for Business Card

Each card will need the following info:
Persons name:
Title:
E-mail:
Phone number:
Shop Address:
Mailing Address:

Requirements
Must have
• Each card will need the following info:
• Persons name:
• Title:
• E-mail:
• Phone number:
• Shop Address:
• Mailing Address:

```html
<!DOCTYPE html>
<html lang="en">
<head>
<meta charset="utf-8">
<title>Ternline Contracting Inc – Business Card</title>
<link href="https://fonts.googleapis.com/css2?family=Open+Sans:wght@400;600;700&display=swap" rel="stylesheet">
<style>
  :root {
    --stage: #2a2a2c;
    --card-dark: #0d0d0d;
    --card-light: #ffffff;
    --orange: #f15a24;
    --grey: #6d6e71;
    --grey-light: #b5b5b7;
    --ink: #4a4a4c;
  }
  * { margin: 0; padding: 0; box-sizing: border-box; }
  html, body { width: 1200px; height: 925px; overflow: hidden; }
  body {
    background: var(--stage);
    font-family: "Open Sans", Arial, sans-serif;
    display: flex;
    align-items: center;
    justify-content: center;
    gap: 40px;
  }
  .card {
    position: relative;
    width: 540px;
    height: 309px;
    overflow: hidden;
    box-shadow: 0 10px 30px rgba(0,0,0,.45);
  }
  .card--front {
    background: radial-gradient(circle at 50% 45%, #1c1c1c 0%, var(--card-dark) 70%);
    display: flex;
    align-items: center;
    justify-content: center;
  }
  .card--back { background: var(--card-light); }
  .card__shapes { position: absolute; inset: 0; }

  .brand {
    display: flex;
    align-items: center;
    gap: 12px;
    color: var(--orange);
    font-weight: 700;
    text-transform: uppercase;
    line-height: 1.05;
  }
  .brand__dot {
    width: 46px; height: 46px;
    border-radius: 50%;
    background: var(--orange);
    flex: none;
  }
  .brand__name { font-size: 28px; letter-spacing: .5px; }
  .brand__sub { font-size: 12px; letter-spacing: 2.2px; }

  .card--back .brand {
    position: absolute;
    left: 34px;
    top: 200px;
  }
  .card--back .brand__dot { width: 36px; height: 36px; }
  .card--back .brand__name { font-size: 22px; }
  .card--back .brand__sub { font-size: 10px; letter-spacing: 1.6px; }

  .divider {
    position: absolute;
    left: 248px;
    top: 52px;
    width: 1px;
    height: 170px;
    background: var(--grey-light);
  }
  .contact {
    position: absolute;
    left: 266px;
    top: 56px;
    color: var(--ink);
    font-size: 12.5px;
    line-height: 1.45;
  }
  .contact__name { color: var(--orange); font-weight: 700; font-size: 14px; }
  .contact__title { margin-bottom: 12px; }
  .contact__address { margin-bottom: 12px; }
  .contact__line { display: flex; align-items: center; gap: 7px; }
  .contact__icon { width: 11px; height: 11px; flex: none; }
</style>
</head>
<body>

  <section class="card card--front" aria-label="Card front">
    <div class="brand">
      <span class="brand__dot"></span>
      <div>
        <div class="brand__name">Ternline</div>
        <div class="brand__sub">Contracting Inc</div>
      </div>
    </div>
  </section>

  <section class="card card--back" aria-label="Card back">
    <svg class="card__shapes" width="540" height="309" viewBox="0 0 540 309">
      <polygon points="0,0 290,0 0,205" fill="var(--orange)"/>
      <polygon points="306,0 322,0 0,236 0,224" fill="var(--grey)"/>
      <polygon points="540,110 540,309 430,309" fill="var(--orange)"/>
    </svg>

    <div class="brand">
      <span class="brand__dot"></span>
      <div>
        <div class="brand__name">Ternline</div>
        <div class="brand__sub">Contracting Inc</div>
      </div>
    </div>

    <div class="divider"></div>

    <div class="contact">
      <div class="contact__name">Corin Vale</div>
      <div class="contact__title">Managing Director</div>
      <div class="contact__address">N. 8 Sample Road,<br>Suite 200, Fairview, WA 00000</div>
      <div class="contact__line">
        <svg class="contact__icon" viewBox="0 0 12 12" aria-hidden="true"><path d="M2.5 1h2l1 3-1.3.9a6.5 6.5 0 0 0 2.9 2.9L8 6.5l3 1v2A1.5 1.5 0 0 1 9.5 11 8.5 8.5 0 0 1 1 2.5 1.5 1.5 0 0 1 2.5 1z" fill="var(--orange)"/></svg>
        555.010.246
      </div>
      <div class="contact__line">
        <svg class="contact__icon" viewBox="0 0 12 12" aria-hidden="true"><rect x="0.5" y="2.5" width="11" height="7.5" rx="1" fill="var(--orange)"/><path d="M1 3l5 3.6L11 3" stroke="#fff" stroke-width="1" fill="none"/></svg>
        info@ternlinecontracting.com
      </div>
    </div>
  </section>

</body>
</html>
```